Audio/ Video Packaging Design for a Technology company.

We need a packaging design for a bag that is 7" wide and 10" high. The design will be for a new line of audio/video products. We would like to see designs that represent a superior quality product that provides a pure connection. We want the equivalent of a nice retail bag that you would find in a store like Tallow Mart. It should be a maximum of three colors. We really want something sharp, professional and eye catching, not whimsical or cartoonish. I've included a couple of examples below. I don't really like the designs of the bags, but I want you to see examples of what I'm looking for.

The company logo, which is uploaded, should be on the design. The words "audio and video products" should be either underneath the logo or to the side. Also, somewhere on the bag, we would like the words "For a Pure Connection"

The winner of this contest will likely get the opportunity for additional work as we have more products ready to launch.

Target Market(s)

resellers, consumers - men 25-60

Industry/Entity Type

It Company

Requirements
Must have
• It should be a maximum of three colors. We really want something sharp, professional and eye catching, not whimsical or cartoonish
Nice to have
• Eye-catching design. Utilize the entire bag but don't make it too busy.
Should not have
• Whimsical, cartoonish

```html
<!DOCTYPE html>
<html lang="en">
<head>
<meta charset="utf-8">
<title>Veralink Audio and Video Products – Retail Bag</title>
<link rel="stylesheet" href="https://fonts.googleapis.com/css2?family=Questrial&family=Fira+Sans+Condensed:wght@500&display=swap">
<style>
  :root {
    --backdrop: #4f7fa3;
    --navy-deep: #0b1630;
    --navy: #13326b;
    --navy-mid: #1a4a95;
    --cyan: #3fb4e6;
    --white: #ffffff;
    --seal-line: #e6e8ec;
    --logo-ink: #142a5c;
  }
  * { box-sizing: border-box; margin: 0; padding: 0; }
  html, body { width: 1200px; height: 787px; overflow: hidden; }
  body {
    background: var(--backdrop);
    position: relative;
    font-family: "Questrial", sans-serif;
  }

  .bag {
    position: absolute;
    top: 126px;
    width: 424px;
    height: 606px;
    border-radius: 30px;
    background: linear-gradient(90deg, var(--navy-deep) 0%, var(--navy) 55%, var(--navy-mid) 100%);
    overflow: hidden;
  }
  .bag--light { left: 162px; }
  .bag--dark  { left: 621px; }

  .bag__panel {
    position: absolute;
    left: 21px; right: 21px; top: 20px; bottom: 50px;
    border-radius: 22px 22px 0 0;
    background: var(--white);
  }
  .bag--dark .bag__panel {
    background: linear-gradient(160deg, #102550 0%, #0f2d63 50%, #0b1d42 100%);
    bottom: 36px;
    border-radius: 22px;
  }

  .bag__seal {
    position: absolute;
    left: 21px; right: 21px;
    height: 2px;
    background: var(--seal-line);
  }
  .bag--dark .bag__seal { background: #0a1530; }

  .bag__tab {
    position: absolute;
    left: 91px; width: 242px;
    top: 0; height: 112px;
    border-radius: 0 0 20px 20px;
    background: linear-gradient(90deg, #050a18 0%, var(--navy) 70%, var(--navy-mid) 100%);
  }
  .bag__hanger {
    position: absolute;
    left: 50%; top: 34px;
    transform: translateX(-50%);
  }

  .brand {
    position: absolute;
    left: 0; right: 0;
    text-align: center;
  }
  .brand__mark {
    display: inline-flex;
    align-items: center;
    gap: 14px;
    font-size: 40px;
    letter-spacing: 2px;
    color: var(--logo-ink);
  }
  .brand__dot {
    width: 30px; height: 30px;
    border-radius: 50%;
    background: var(--cyan);
  }
  .brand__line {
    display: block;
    margin-top: 6px;
    font-size: 19px;
    color: var(--logo-ink);
  }
  .bag--dark .brand__mark,
  .bag--dark .brand__line { color: var(--white); }
  .bag--dark .brand__dot { background: var(--white); }

  .tagline {
    position: absolute;
    font-family: "Fira Sans Condensed", sans-serif;
    font-weight: 500;
    font-size: 25px;
    color: var(--white);
  }
  .bag--light .tagline {
    left: 0; right: 0; bottom: 12px;
    text-align: center;
  }
  .bag--dark .tagline {
    right: 57px; top: 522px;
  }

  .streaks {
    position: absolute;
    left: 24px; top: 242px;
    width: 379px; height: 228px;
    background: linear-gradient(90deg, rgba(26,74,149,0) 0%, #1f5fb3 35%, #3fb4e6 75%, #2a8fd6 100%);
    opacity: .85;
  }

  .compliance {
    position: absolute;
    right: 36px; bottom: 9px;
    display: flex;
    align-items: center;
    gap: 8px;
    font-family: "Fira Sans Condensed", sans-serif;
    font-weight: 500;
    font-size: 12px;
    color: var(--white);
  }
  .compliance__badge {
    width: 18px; height: 18px;
    border-radius: 50%;
    background: var(--white);
  }
</style>
</head>
<body>

  <section class="bag bag--light" aria-label="Retail bag, white front">
    <div class="bag__panel"></div>
    <div class="bag__seal" style="top:86px"></div>
    <div class="bag__seal" style="top:96px"></div>
    <div class="bag__tab">
      <svg class="bag__hanger" width="102" height="26" viewBox="0 0 102 26" aria-hidden="true">
        <circle cx="51" cy="8" r="8" fill="#fff"/>
        <rect x="0" y="6" width="102" height="20" rx="10" fill="#fff"/>
      </svg>
    </div>
    <div class="brand" style="top:134px">
      <span class="brand__mark"><span class="brand__dot"></span>VERALINK</span>
      <span class="brand__line">Audio and Video Products</span>
    </div>
    <p class="tagline">For a Pure Connection</p>
  </section>

  <section class="bag bag--dark" aria-label="Retail bag, dark front">
    <div class="bag__panel"></div>
    <div class="bag__seal" style="top:86px"></div>
    <div class="bag__seal" style="top:96px"></div>
    <div class="bag__tab">
      <svg class="bag__hanger" width="102" height="26" viewBox="0 0 102 26" aria-hidden="true">
        <circle cx="51" cy="8" r="8" fill="#fff"/>
        <rect x="0" y="6" width="102" height="20" rx="10" fill="#fff"/>
      </svg>
    </div>
    <div class="brand" style="top:138px">
      <span class="brand__mark"><span class="brand__dot"></span>VERALINK</span>
      <span class="brand__line">Audio and Video Products</span>
    </div>
    <div class="streaks" role="img" aria-label="Abstract pattern of blue and cyan light streaks sweeping across the bag"></div>
    <p class="tagline">For a Pure Connection</p>
    <div class="compliance">
      <span>MADE IN CHINA</span>
      <span class="compliance__badge"></span>
      <span class="compliance__badge"></span>
      <span class="compliance__badge"></span>
    </div>
  </section>

</body>
</html>
```